A Health & Fitness Website selling saunas and Cold tubs

www.dockvaultguys.com, www.frostlanterguys, www.chillharborguys
Design a website
We are selling saunas, infrared saunas, cold plunge tubs, and massage chairs to financially successful MEN.
We want professional, simple, masculine with a touch of sexy.
One section for each… saunas, cold plunge tubs, massage chairs.
Each will have at least two buy links to their affiliate/supplier/store.
The landing page / opening page / needs big & bold; a full screen image? a great picture showing the warmth of a sauna? Need your ideas
The pictures are everything.

The Website for our book
https://maebelsvigorguys.com/

Coding

Coded - Design and coding required

Number of Pages Required

1 page

Requirements
Must have
• Great pictures

```html
<!DOCTYPE html>
<html lang="en">
<head>
<meta charset="utf-8">
<title>Maebel Vigor Fitness for Men</title>
<link rel="stylesheet" href="https://fonts.googleapis.com/css2?family=Oswald:wght@500;600&family=Poppins:wght@400;500;600&display=swap">
<style>
:root{
  --ink:#111111;
  --text:#333333;
  --muted:#555555;
  --panel:#f6f6f6;
  --white:#ffffff;
  --black:#000000;
  --star:#f2b705;
  --line:#dcdcdc;
}
*{margin:0;padding:0;box-sizing:border-box}
html,body{width:1200px;height:5386px;overflow:hidden;background:var(--white)}
body{position:relative;font-family:"Poppins",sans-serif;color:var(--text)}
.abs{position:absolute}
.display{font-family:"Oswald",sans-serif;font-weight:500;text-transform:uppercase;color:var(--ink);letter-spacing:.2px}
.photo{position:absolute}

/* hero */
.hero{position:absolute;left:0;top:0;width:1200px;height:563px;
  background:linear-gradient(100deg,#2b2b2e 0%,#4a4543 30%,#6b5258 50%,#3d3a3c 75%,#1f1f22 100%);
  clip-path:polygon(0 0,100% 0,100% 89%,0 100%)}
.hero::after{content:"";position:absolute;inset:0;background:rgba(0,0,0,.35)}
.brand{position:absolute;left:140px;top:22px;width:96px;height:96px;border-radius:50%;border:3px solid var(--white);
  display:flex;align-items:center;justify-content:center;text-align:center;z-index:2;
  font-family:"Poppins",sans-serif;font-weight:600;font-size:11px;line-height:1.25;color:var(--white)}
.nav{position:absolute;top:56px;left:858px;display:flex;gap:13px;z-index:2}
.nav a{display:block;width:94px;height:28px;line-height:28px;background:var(--black);color:var(--white);
  text-align:center;font-size:10px;font-weight:500;text-decoration:none;text-transform:uppercase}
.hero-copy{position:absolute;left:0;width:1200px;top:224px;text-align:center;z-index:2;color:var(--white)}
.hero-copy p{font-size:15px;font-weight:500}
.hero-copy h1{font-family:"Oswald",sans-serif;font-weight:500;font-size:44px;line-height:54px;text-transform:uppercase;margin-top:2px}

/* intro */
.intro{position:absolute;top:640px;left:0;width:1200px;text-align:center}
.intro h2{font-size:32px;line-height:44px}
.intro p{font-size:15px;line-height:27px;color:var(--text)}

/* product cards */
.card-bg{position:absolute;background:var(--panel)}
.product{position:absolute;width:380px}
.icon-badge{width:64px;height:64px;border-radius:50%;background:var(--black);display:flex;align-items:center;justify-content:center}
.product h3{font-size:32px;line-height:40px;margin-top:14px}
.product p{font-size:12.5px;line-height:21.5px;color:var(--muted);margin-top:12px}

/* bands */
.band{position:absolute;left:0;width:1200px;display:flex;align-items:center;justify-content:center;text-align:center}
.band h2{font-family:"Oswald",sans-serif;font-weight:500;font-size:42px;line-height:52px;text-transform:uppercase;color:var(--white);position:relative;z-index:2}
.band-circ{top:2175px;height:363px;background:linear-gradient(180deg,#3a3a3c,#1c1c1e);clip-path:polygon(0 0,100% 0,100% 88%,0 100%)}
.band-circ::before{content:"";position:absolute;inset:0;background:rgba(0,0,0,.35)}
.band-indiv{top:3200px;height:365px;background:linear-gradient(180deg,#1e1e20,#111113);clip-path:polygon(0 1%,100% 0,100% 95%,0 100%)}

/* benefits */
.benefits-head{position:absolute;top:2616px;left:0;width:1200px;text-align:center;font-size:32px;line-height:40px}
.benefits{position:absolute;left:203px;top:2716px;list-style:none}
.benefits li{display:flex;align-items:center;gap:7px;height:31.4px;font-size:14px;color:var(--ink)}
.benefits li.strong{font-weight:500}
.benefits svg{flex:none}

/* reviews */
.reviews-head{position:absolute;top:3646px;left:0;width:1200px;text-align:center;font-size:32px;line-height:42px}
.review{position:absolute;width:280px;background:var(--white);box-shadow:0 2px 12px rgba(0,0,0,.08);padding:92px 18px 0 18px}
.quote{position:absolute;left:18px;top:-2px;width:62px;height:62px;border-radius:50%;border:3px solid var(--ink);background:var(--white);
  font-family:"Oswald",sans-serif;font-size:44px;line-height:70px;text-align:center;color:var(--ink)}
.review p{font-size:12px;line-height:21.5px;color:var(--muted)}
.stars{position:absolute;left:18px;bottom:22px;color:var(--star);font-size:13px;letter-spacing:1px}
.load-more{position:absolute;left:538px;top:4420px;width:122px;height:34px;background:var(--black);color:var(--white);
  font-size:11px;font-weight:500;text-transform:uppercase;display:flex;align-items:center;justify-content:center;gap:6px;text-decoration:none}

.closing{position:absolute;left:647px;top:4640px;font-size:46px;line-height:52px}

/* footer */
.footer-shape{position:absolute;left:0;top:5000px;width:1200px;height:386px}
.footer-brand{position:absolute;left:543px;top:5072px;width:114px;height:114px;border-radius:50%;border:3px solid var(--white);
  display:flex;align-items:center;justify-content:center;text-align:center;font-weight:600;font-size:13px;line-height:1.3;color:var(--white)}
.contact{position:absolute;top:5244px;display:flex;gap:10px;color:var(--white);font-size:12px;line-height:17px}
.contact b{font-weight:600;display:block}
.copyright{position:absolute;left:142px;top:5340px;font-size:12px;color:var(--white)}
.social{position:absolute;left:922px;top:5334px;display:flex;gap:6px}
.social span{width:30px;height:30px;border-radius:50%;border:2px solid var(--white);display:block}
</style>
</head>
<body>

<header>
  <div class="hero" role="img" aria-label="Photo of a man and a woman lifting dumbbells in a gym"></div>
  <div class="brand">MAEBEL<br>VIGOR<br>FITNESS</div>
  <nav class="nav"><a href="#">Affiliate</a><a href="#">Store</a></nav>
  <div class="hero-copy">
    <p>Maebel Vigor Fitness for Men</p>
    <h1>Top of the line health products exclusively<br>for the financially successful</h1>
  </div>
</header>

<section class="intro">
  <h2 class="display">Dramatically improve your health without exercise</h2>
  <p>Successful Men Recognize the Importance of Their Health and Make it a Priority.<br>It's Your Time. You've Earned it.</p>
</section>

<!-- saunas -->
<div class="card-bg" style="left:246px;top:760px;width:818px;height:436px"></div>
<div class="photo" style="left:142px;top:812px;width:424px;height:332px;background:linear-gradient(120deg,#3b3f44,#6a5a4e 55%,#2c2f33)" role="img" aria-label="Photo of a man with a towel in a locker room"></div>
<article class="product" style="left:617px;top:853px">
  <div class="icon-badge"><svg width="34" height="34" viewBox="0 0 34 34" fill="none" stroke="#fff" stroke-width="2"><rect x="5" y="18" width="24" height="10"/><path d="M10 14c-2-2 2-4 0-6M17 14c-2-2 2-4 0-6M24 14c-2-2 2-4 0-6"/></svg></div>
  <h3 class="display">Saunas</h3>
  <p>Lorem Ipsum is simply dummy text of the printing and typesetting industry. Lorem Ipsum has been the industry's standard dummy text ever since the 1500s, when an unknown printer took a galley of type and scrambled it to make a type specimen book. It has survived not only five centuries.</p>
</article>

<!-- cold plunge -->
<div class="card-bg" style="left:134px;top:1206px;width:816px;height:437px"></div>
<div class="photo" style="left:632px;top:1258px;width:422px;height:332px;background:linear-gradient(135deg,#7fd6d8,#2aa6b3 55%,#a9e4e3)" role="img" aria-label="Photo of a man resting in a cold plunge pool"></div>
<article class="product" style="left:196px;top:1300px">
  <div class="icon-badge"><svg width="34" height="34" viewBox="0 0 34 34" fill="none" stroke="#fff" stroke-width="2"><path d="M4 20h26v4a4 4 0 0 1-4 4H8a4 4 0 0 1-4-4z"/><path d="M9 16c2-2 4 2 6 0s4 2 6 0 4 2 6 0"/><circle cx="24" cy="8" r="3"/></svg></div>
  <h3 class="display">Cold plunge tubs</h3>
  <p>Lorem Ipsum is simply dummy text of the printing and typesetting industry. Lorem Ipsum has been the industry's standard dummy text ever since the 1500s, when an unknown printer took a galley of type and scrambled it to make a type specimen book. It has survived not only five centuries.</p>
</article>

<!-- massage chairs -->
<div class="card-bg" style="left:246px;top:1653px;width:814px;height:436px"></div>
<div class="photo" style="left:142px;top:1705px;width:422px;height:332px;background:linear-gradient(120deg,#d9d6d2,#4a4547 50%,#c9c4bf)" role="img" aria-label="Photo of a man and a woman relaxing in massage chairs"></div>
<article class="product" style="left:615px;top:1746px">
  <div class="icon-badge"><svg width="34" height="34" viewBox="0 0 34 34" fill="none" stroke="#fff" stroke-width="2"><path d="M9 6c0 8 2 14 8 16h9"/><path d="M12 22l-3 7M24 22l3 7"/><circle cx="11" cy="7" r="3"/></svg></div>
  <h3 class="display">Massage chairs</h3>
  <p>Lorem Ipsum is simply dummy text of the printing and typesetting industry. Lorem Ipsum has been the industry's standard dummy text ever since the 1500s, when an unknown printer took a galley of type and scrambled it to make a type specimen book. It has survived not only five centuries.</p>
</article>

<section class="band band-circ" role="img" aria-label="Photo of a row of treadmills in a gym">
  <h2 style="margin-top:-30px">A mans body thrives on circulation<br>and it doesn't care how you get it</h2>
</section>

<h2 class="benefits-head display">When there's no time for exercise.<br>Use hot, cold, or massage. The benefits are numerous.</h2>
<ul class="benefits">
  <li><svg width="16" height="16" viewBox="0 0 16 16"><circle cx="8" cy="8" r="8" fill="#111"/><path d="M4.5 8.2l2.3 2.3 4.7-4.8" stroke="#fff" stroke-width="1.8" fill="none"/></svg>Relieve Stress</li>
  <li><svg width="16" height="16" viewBox="0 0 16 16"><circle cx="8" cy="8" r="8" fill="#111"/><path d="M4.5 8.2l2.3 2.3 4.7-4.8" stroke="#fff" stroke-width="1.8" fill="none"/></svg>Detox Your Pores</li>
  <li><svg width="16" height="16" viewBox="0 0 16 16"><circle cx="8" cy="8" r="8" fill="#111"/><path d="M4.5 8.2l2.3 2.3 4.7-4.8" stroke="#fff" stroke-width="1.8" fill="none"/></svg>Sleep BetterRelieve Muscle Tension</li>
  <li><svg width="16" height="16" viewBox="0 0 16 16"><circle cx="8" cy="8" r="8" fill="#111"/><path d="M4.5 8.2l2.3 2.3 4.7-4.8" stroke="#fff" stroke-width="1.8" fill="none"/></svg>Boost Energy LevelsIncrease Testosterone</li>
  <li><svg width="16" height="16" viewBox="0 0 16 16"><circle cx="8" cy="8" r="8" fill="#111"/><path d="M4.5 8.2l2.3 2.3 4.7-4.8" stroke="#fff" stroke-width="1.8" fill="none"/></svg>Reduce Inflammation</li>
  <li class="strong"><svg width="16" height="16" viewBox="0 0 16 16"><circle cx="8" cy="8" r="8" fill="#111"/><path d="M4.5 8.2l2.3 2.3 4.7-4.8" stroke="#fff" stroke-width="1.8" fill="none"/></svg>Increase Immunity</li>
  <li><svg width="16" height="16" viewBox="0 0 16 16"><circle cx="8" cy="8" r="8" fill="#111"/><path d="M4.5 8.2l2.3 2.3 4.7-4.8" stroke="#fff" stroke-width="1.8" fill="none"/></svg>Reduce Depression</li>
  <li class="strong"><svg width="16" height="16" viewBox="0 0 16 16"><circle cx="8" cy="8" r="8" fill="#111"/><path d="M4.5 8.2l2.3 2.3 4.7-4.8" stroke="#fff" stroke-width="1.8" fill="none"/></svg>Alleviate Joint Pain</li>
  <li class="strong"><svg width="16" height="16" viewBox="0 0 16 16"><circle cx="8" cy="8" r="8" fill="#111"/><path d="M4.5 8.2l2.3 2.3 4.7-4.8" stroke="#fff" stroke-width="1.8" fill="none"/></svg>Healthier Skin</li>
  <li><svg width="16" height="16" viewBox="0 0 16 16"><circle cx="8" cy="8" r="8" fill="#111"/><path d="M4.5 8.2l2.3 2.3 4.7-4.8" stroke="#fff" stroke-width="1.8" fill="none"/></svg>Lower the Risk of Cardiovascular Disease</li>
  <li><svg width="16" height="16" viewBox="0 0 16 16"><circle cx="8" cy="8" r="8" fill="#111"/><path d="M4.5 8.2l2.3 2.3 4.7-4.8" stroke="#fff" stroke-width="1.8" fill="none"/></svg>Increase Metabolism</li>
  <li><svg width="16" height="16" viewBox="0 0 16 16"><circle cx="8" cy="8" r="8" fill="#111"/><path d="M4.5 8.2l2.3 2.3 4.7-4.8" stroke="#fff" stroke-width="1.8" fill="none"/></svg>Promote Weight Loss</li>
  <li><svg width="16" height="16" viewBox="0 0 16 16"><circle cx="8" cy="8" r="8" fill="#111"/><path d="M4.5 8.2l2.3 2.3 4.7-4.8" stroke="#fff" stroke-width="1.8" fill="none"/></svg>A Longer &amp; Healthier Life</li>
</ul>
<div class="photo" style="left:605px;top:2719px;width:388px;height:397px;background:linear-gradient(150deg,#5a5a5e,#8b7f80 50%,#2f2f33)" role="img" aria-label="Photo of a trainer coaching a woman lifting dumbbells"></div>

<section class="band band-indiv"><h2>Specific improvements<br>will be individual to you</h2></section>
<div class="photo" style="left:0;top:3131px;width:210px;height:420px;background:linear-gradient(180deg,#b68c72,#7a5a48 60%,#3a3a3e)" role="img" aria-label="Photo of a muscular man holding a dumbbell"></div>
<div class="photo" style="left:1030px;top:3131px;width:170px;height:400px;background:linear-gradient(180deg,#d9b796,#c9a07e 50%,#e5e5e5)" role="img" aria-label="Photo of a fit woman in a sports top"></div>

<h2 class="reviews-head display">Customer reviews</h2>
<article class="review" style="left:142px;top:3704px;height:324px"><div class="quote">“</div><p>Successful Men Recognize the Importance of Their Health and Make it a Priority. It's Your Time. You've Earned it.</p><div class="stars">★★★★★</div></article>
<article class="review" style="left:459px;top:3704px;height:324px"><div class="quote">“</div><p>I had no idea how much inflammation I had in my body. It wasn't until the relief I got from my cold plunge that I realized how bad joints were. It's been a life changing relief.</p><div class="stars">★★★★★</div></article>
<article class="review" style="left:776px;top:3704px;height:324px"><div class="quote">“</div><p>I love a good massage but making an appointment is almost impossible with my schedule. The chair is always there. I climb in and let it do its thing. I forget about work so much that it usually turns in to a power nap.</p><div class="stars">★★★★★</div></article>
<article class="review" style="left:142px;top:4095px;height:296px"><div class="quote">“</div><p>I bought the massage chair for my late evening relaxation. When I get home late I don't want to get wet or sweaty, I just need to relax. The chair does the trick.</p><div class="stars">★★★★★</div></article>
<article class="review" style="left:459px;top:4095px;height:296px"><div class="quote">“</div><p>My massage chair has been a life saver. Having back pain for years the chair gives me the relief I need. I can dial in for a deep massage or gentle pressure. I would never be able to get a daily massage any other way</p><div class="stars">★★★★★</div></article>
<article class="review" style="left:776px;top:4095px;height:296px"><div class="quote">“</div><p>Having a sauna in my home has been a game-changer. After a long day at work, I step into warmth and it's total relaxation. The heat and gentle steam instantly melts me. It's like a mini vacation without leaving home. I can't imagine life without my sauna.</p><div class="stars">★★★★★</div></article>
<a class="load-more" href="#">Load more <svg width="8" height="6" viewBox="0 0 8 6"><path d="M1 1l3 3 3-3" stroke="#fff" stroke-width="1.4" fill="none"/></svg></a>

<div class="photo" style="left:142px;top:4510px;width:386px;height:395px;background:linear-gradient(140deg,#6a6a6e,#9a8a86 50%,#3a3a3e)" role="img" aria-label="Photo of a woman training with a man on a weight bench"></div>
<h2 class="closing display">Everything works<br>better with increased<br>blood flow</h2>

<footer>
  <svg class="footer-shape" viewBox="0 0 1200 386" preserveAspectRatio="none">
    <path d="M0 42Q600 -20 1200 42V386H0Z" fill="#000"/>
    <path d="M0 34Q600 -28 1200 34" stroke="#cfcfcf" stroke-width="4" fill="none"/>
  </svg>
  <div class="footer-brand">MAEBEL<br>VIGOR<br>FITNESS</div>
  <div class="contact" style="left:142px">
    <svg width="34" height="26" viewBox="0 0 34 26" fill="none" stroke="#fff" stroke-width="1.6"><path d="M3 12L17 2l14 10M6 10v14h22V10"/><rect x="14" y="15" width="6" height="9"/></svg>
    <div><b>Address</b>1234 Lorem Ipsum Suite 700<br>Lorem, LA 1234</div>
  </div>
  <div class="contact" style="left:547px">
    <svg width="30" height="26" viewBox="0 0 30 26" fill="none" stroke="#fff" stroke-width="1.6"><path d="M5 3l5 1 2 6-3 2a14 14 0 0 0 7 7l2-3 6 2 1 5c-12 1-21-8-20-20z"/></svg>
    <div><b>Phone</b>(123) 456-7890</div>
  </div>
  <div class="contact" style="left:883px">
    <svg width="30" height="24" viewBox="0 0 30 24" fill="none" stroke="#fff" stroke-width="1.6"><rect x="2" y="4" width="26" height="17"/><path d="M2 4l13 10L28 4"/></svg>
    <div><b>Email</b>info@maebelvigor.com</div>
  </div>
  <p class="copyright">© 2024 Maebel Vigor Fitness.com | Allrights Reserved</p>
  <div class="social" aria-label="Social links"><span></span><span></span><span></span><span></span></div>
</footer>

</body>
</html>
```